Business Card Design

I am a GP with interest in Dermatology and Aesthetic Medicin, performing Botulinum Toxin Type A and Dermal Fillers treatmets in Cosmetic Dermatology clinic.

I am looking for a white colour, good quality white paper card may be of some special texture with black calligraphic writing but easy to read and not to wiggly- professional- looking.

Really appreciate your help.

Marisha

Cosmetic Dermatology Clinic

Dr Marisha Volkovska, MBBS, MRCGP, DPD

Tel: 07941 586 217
marisha@medpracto.org.uk

```html
<!DOCTYPE html>
<html lang="en">
<head>
<meta charset="utf-8">
<title>Cosmetic Dermatology Clinic – Business Card</title>
<link rel="stylesheet" href="https://fonts.googleapis.com/css2?family=Josefin+Sans:wght@300;400&family=Oswald:wght@600&family=Quicksand:wght@500&display=swap">
<style>
  :root {
    --backdrop: #ece9e4;
    --paper: #ffffff;
    --paper-shade: #f1f1f1;
    --ink: #1c1c1c;
    --ink-soft: #3a3a3a;
    --night: #1e1e1e;
    --steel: #8e8e8e;
    --gold-light: #e4d7b6;
    --gold-dark: #b9a473;
    --on-night: #f4f4f4;
  }
  * { box-sizing: border-box; margin: 0; padding: 0; }
  html, body { width: 1200px; height: 983px; overflow: hidden; }
  body {
    background: var(--backdrop);
    font-family: "Josefin Sans", sans-serif;
    color: var(--ink);
  }
  .sheet {
    position: relative;
    width: 1200px;
    height: 983px;
    display: flex;
    align-items: center;
    justify-content: center;
    gap: 80px;
  }
  .card {
    position: relative;
    width: 400px;
    height: 700px;
    background: var(--paper);
    box-shadow: 0 18px 40px rgba(0,0,0,0.18);
    overflow: hidden;
  }
  .card-shapes { position: absolute; inset: 0; width: 100%; height: 100%; }
  .clinic-name {
    position: absolute;
    right: 40px;
    text-align: right;
    font-weight: 300;
    font-size: 34px;
    line-height: 1.15;
    letter-spacing: 0.5px;
    color: var(--ink);
  }
  .card--back .clinic-name { top: 190px; }
  .card--front .clinic-name { top: 110px; }

  .person {
    position: absolute;
    top: 270px;
    right: 40px;
    left: 30px;
    text-align: right;
  }
  .person-name {
    font-family: "Oswald", sans-serif;
    font-weight: 600;
    font-size: 28px;
    letter-spacing: 1px;
    line-height: 1.1;
    white-space: nowrap;
  }
  .person-role {
    font-family: "Josefin Sans", sans-serif;
    font-weight: 400;
    font-size: 18px;
    letter-spacing: 2px;
  }
  .contacts {
    position: absolute;
    top: 370px;
    left: 30px;
    right: 30px;
    display: grid;
    grid-template-columns: auto auto;
    justify-content: space-between;
    row-gap: 18px;
    column-gap: 14px;
    font-family: "Quicksand", sans-serif;
    font-weight: 500;
    font-size: 13px;
    color: var(--ink-soft);
  }
  .contact { display: flex; align-items: center; gap: 8px; white-space: nowrap; }
  .contact-icon { width: 18px; height: 18px; flex: none; }

  .address {
    position: absolute;
    left: 0; right: 0;
    top: 560px;
    text-align: center;
    color: var(--on-night);
  }
  .address-pin { width: 34px; height: 34px; display: block; margin: 0 auto 14px; }
  .address-lines {
    font-family: "Quicksand", sans-serif;
    font-weight: 500;
    font-size: 15px;
    line-height: 1.6;
    letter-spacing: 0.5px;
  }
</style>
</head>
<body>
<main class="sheet">

  <section class="card card--back" aria-label="Card back">
    <svg class="card-shapes" viewBox="0 0 400 700" aria-hidden="true">
      <defs>
        <linearGradient id="paperFadeBack" x1="0" y1="0" x2="0" y2="1">
          <stop offset="0" stop-color="var(--paper)"/>
          <stop offset="1" stop-color="var(--paper-shade)"/>
        </linearGradient>
      </defs>
      <rect width="400" height="700" fill="url(#paperFadeBack)"/>
      <polygon points="0,430 200,500 400,430 400,700 0,700" fill="var(--steel)"/>
      <polygon points="0,446 200,516 400,446 400,700 0,700" fill="var(--night)"/>
    </svg>
    <h1 class="clinic-name">Cosmetic<br>Dermatology Clinic</h1>
    <div class="address">
      <svg class="address-pin" viewBox="0 0 34 34" aria-hidden="true">
        <circle cx="17" cy="17" r="15.5" fill="none" stroke="var(--on-night)" stroke-width="2"/>
        <path d="M17 8a6 6 0 0 0-6 6c0 4.5 6 11 6 11s6-6.5 6-11a6 6 0 0 0-6-6z" fill="var(--on-night)"/>
        <circle cx="17" cy="14" r="2.2" fill="var(--night)"/>
      </svg>
      <p class="address-lines">14 Elmwood Road,<br>2nd floor Suite B.</p>
    </div>
  </section>

  <section class="card card--front" aria-label="Card front">
    <svg class="card-shapes" viewBox="0 0 400 700" aria-hidden="true">
      <defs>
        <linearGradient id="goldBand" x1="0" y1="0" x2="1" y2="0">
          <stop offset="0" stop-color="var(--gold-light)"/>
          <stop offset="1" stop-color="var(--gold-dark)"/>
        </linearGradient>
      </defs>
      <rect width="400" height="700" fill="var(--paper)"/>
      <polygon points="0,0 400,0 400,60 200,22 0,60" fill="url(#goldBand)"/>
      <polygon points="0,530 200,580 400,530 400,700 0,700" fill="var(--steel)"/>
      <polygon points="0,546 200,596 400,546 400,700 0,700" fill="var(--night)"/>
    </svg>
    <h1 class="clinic-name">Cosmetic<br>Dermatology Clinic</h1>
    <div class="person">
      <p class="person-name">DR MARISHA VOLKOVSKA</p>
      <p class="person-role">GENERAL MANAGER</p>
    </div>
    <div class="contacts">
      <p class="contact">
        <svg class="contact-icon" viewBox="0 0 18 18" aria-hidden="true"><circle cx="9" cy="9" r="8" fill="none" stroke="currentColor" stroke-width="1.3"/><path d="M6.2 4.8l1.4 1.6-.8 1.2c.5 1.2 1.3 2 2.5 2.6l1.2-.8 1.6 1.4-.9 1.4c-2.9-.4-5.3-2.8-5.8-5.8z" fill="currentColor"/></svg>
        020 7946 0321
      </p>
      <p class="contact">
        <svg class="contact-icon" viewBox="0 0 18 18" aria-hidden="true"><circle cx="9" cy="9" r="8" fill="none" stroke="currentColor" stroke-width="1.3"/><rect x="4.5" y="6" width="9" height="6.5" rx="1" fill="currentColor"/><path d="M4.8 6.4L9 9.6l4.2-3.2" fill="none" stroke="var(--paper)" stroke-width="1"/></svg>
        marisha@medpracto.org.uk
      </p>
      <p class="contact">
        <svg class="contact-icon" viewBox="0 0 18 18" aria-hidden="true"><circle cx="9" cy="9" r="8" fill="none" stroke="currentColor" stroke-width="1.3"/><rect x="5.5" y="4" width="7" height="10" rx="1.2" fill="currentColor"/><rect x="6.6" y="5.3" width="4.8" height="6.4" fill="var(--paper)"/></svg>
        07941 586 217
      </p>
      <p class="contact">
        <svg class="contact-icon" viewBox="0 0 18 18" aria-hidden="true"><circle cx="9" cy="9" r="8" fill="none" stroke="currentColor" stroke-width="1.3"/><circle cx="9" cy="9" r="4.6" fill="none" stroke="currentColor" stroke-width="1.2"/><path d="M4.4 9h9.2M9 4.4c-2 2.6-2 6.6 0 9.2M9 4.4c2 2.6 2 6.6 0 9.2" fill="none" stroke="currentColor" stroke-width="1"/></svg>
        www.medpracto.org.uk
      </p>
    </div>
  </section>

</main>
</body>
</html>
```